Corwin Beacon Lighting - Commercial & Residential Landscape Lighting

Landscape Lighting Services & Design: Create a website for our landscape lighting company. We would like the design to be tailored around this description:
Illuminate with Confidence. Designed with Precision. Installed with Care.
Locally and veteran-owned, we take pride in transforming outdoor spaces through innovative lighting solutions tailored to your vision. From landscape and holiday lighting to permanent installations, our effortless process and expert design deliver breathtaking results and lasting curb appeal. Backed by a lifetime warranty and quarterly service options, our commitment to quality and customer satisfaction is unwavering. Try before you buy and experience your home in a whole new light with our complimentary demo kit — see the stunning effects before you decide.
- Also, add in this information as well; Outdoor Lighting not only beautifies spaces but also significantly enhances safety by illuminating your home or business. Beautifully lit entrances deter potential intruders, making your home a safer place for your loved ones. we also offer quarterly service plans to ensure lighting equipment continues to operate & illuminate effectively throughout the year. Also mention we provide free estimates and we are offering a 10% discount to military, veterans, and first responders.

Target Market(s)

Luxury market

Industry/Entity Type

Landscape Lighting - Residential & Commercial Lighting Services

Coding

Coded - Design and coding required

Number of Pages Required

2 page

Colors
00AB8E
00BBA5
67D7C9
C6EFE9
E9F9F6
59FF00
82FF00
B8FF75
E3FFCB
F4FFEA
FFC000
F8CF3A
FAE287
FDF2CF
FEFAEE

Requirements
Must have
• a lead generation button where people can submit their information for us to reach out to them and schedule their free estimate, homepage, about page, contact page, products and services page, user friendly, easy to navigate, and it also must be engaging and eye popping, as well as appealing to the luxury market. Please use colors; verdent green, dark green, ivory, and sunny yellow. Also, include an about page that references our story; Derek is retired Army and he opened a fitness studio in 2017 with his wife Jolene. He has installed low voltage lighting in every home he lived in and for his friends and family over the years and decided to open his own business because he is passionate about beautifying outdoor landscapes and highlighting a properties full potential, not only in the day but at night as well all while providing safety and security for his clients. Having a deep respect for nature and landscaping, he wants to provide the same care and quality to each of his clients as he has in the fitness industry for decades. He believes small businesses are the back bone of America and he's excited to provide a service that is all to often neglected in the design of a home.
Nice to have
• I would like to have a clear intent and purpose, engaging web design, clear call to action, optimized for search engines, mobile friendy design, security measures, credibility indicators

```html
<!DOCTYPE html>
<html lang="en">
<head>
<meta charset="utf-8">
<title>Corwin Beacon Lighting – Residential &amp; Commercial Landscape Lighting</title>
<link rel="stylesheet" href="https://fonts.googleapis.com/css2?family=Montserrat:wght@400;500;600;700&family=Roboto:wght@400;500&display=swap">
<style>
:root{
  --green-dark:#17644a;
  --green-deep:#0f4c37;
  --ivory:#f3f6e7;
  --yellow:#f5c83a;
  --ink:#1f2a24;
  --muted:#4a4f4b;
  --white:#ffffff;
  --line:#b9bdb9;
}
*{box-sizing:border-box;margin:0;padding:0}
html,body{width:1200px;height:3986px;overflow:hidden}
body{position:relative;font-family:"Montserrat",sans-serif;color:var(--ink);background:var(--white)}
a{color:inherit;text-decoration:none}
.abs{position:absolute}
.btn{display:inline-block;background:var(--yellow);color:var(--ink);font-weight:500;font-size:16px;border-radius:6px;padding:0 20px;line-height:36px}

/* header */
.site-header{position:absolute;left:0;top:0;width:1200px;height:100px;background:var(--green-dark)}
.brand{position:absolute;left:94px;top:36px;font-size:24px;font-weight:600;color:var(--yellow);display:flex;align-items:center;gap:10px}
.brand-dot{width:14px;height:14px;border-radius:50%;background:var(--yellow)}
.main-nav{position:absolute;right:114px;top:38px;display:flex;gap:40px;font-size:17px;color:#e9efe9}
.main-nav .active{color:var(--white);font-weight:600}

/* hero */
.hero{position:absolute;left:0;top:100px;width:1200px;height:570px;background:linear-gradient(120deg,#1d221f 0%,#2c332c 45%,#3c4436 100%)}
.hero-photo{position:absolute;left:0;top:0;width:1200px;height:570px;clip-path:polygon(815px 0,1200px 0,1200px 570px,643px 570px,643px 470px);background:linear-gradient(160deg,#c9d3d1 0%,#9aa59b 35%,#6f7a55 65%,#3f4537 100%)}
.hero-title{position:absolute;left:94px;top:226px;font-size:43px;font-weight:700;line-height:50px;color:var(--white)}
.hero-text{position:absolute;left:94px;top:402px;width:540px;font-size:18px;line-height:26px;color:var(--white)}
.hero .btn{position:absolute;left:94px;top:495px}

/* services */
.services{position:absolute;left:0;top:670px;width:1200px;height:633px;background:var(--ivory)}
.section-title{font-size:40px;font-weight:600;color:var(--green-dark);text-align:center}
.services .section-title{position:absolute;left:0;top:75px;width:1200px}
.service{position:absolute;top:156px;width:302px}
.service-photo{width:302px;height:222px}
.service h3{margin-top:28px;font-size:20px;font-weight:500}
.service ul{list-style:none;margin-top:18px}
.service li{font-size:14.5px;color:var(--muted);line-height:24px;display:flex;align-items:center;gap:13px;padding-left:2px}
.service a.more{display:inline-block;margin-top:12px;margin-left:2px;font-size:15px;color:var(--green-dark);text-decoration:underline}

/* demo band */
.demo-band{position:absolute;left:0;top:1303px;width:1200px;height:209px;background:var(--green-dark);text-align:center;color:var(--white)}
.demo-band p{margin:38px auto 0;width:880px;font-size:23px;line-height:34px}
.demo-band .btn{margin-top:24px}

/* story */
.story-title{position:absolute;left:111px;top:1585px;font-size:42px;font-weight:600;color:var(--green-dark)}
.story-text{position:absolute;left:113px;top:1670px;width:525px;font-size:16px;line-height:25.6px;color:var(--muted)}
.story .btn{position:absolute;left:113px;top:1865px}
.story-photo{position:absolute;left:673px;top:1597px;width:416px;height:305px;background:linear-gradient(120deg,#5a6a6f 0%,#8f9ea2 45%,#3d6b8f 75%,#2c3b44 100%)}

/* features */
.feature{position:absolute;top:1990px;width:200px;text-align:center;font-family:"Roboto",sans-serif;font-size:17px;font-weight:500;line-height:26px;color:var(--ink)}
.feature-icon{display:block;margin:0 auto 16px;width:136px;height:136px}
.feature-sep{position:absolute;top:2048px;width:2px;height:72px;background:var(--green-dark)}

/* projects */
.projects-bg{position:absolute;left:0;top:2263px;width:1200px;height:373px;background:var(--ivory)}
.projects-title{position:absolute;left:109px;top:2338px;font-size:41px;font-weight:600;line-height:50px;color:var(--green-dark)}
.projects-text{position:absolute;left:618px;top:2362px;width:470px;font-size:16px;line-height:26px;color:var(--muted)}
.compare{position:absolute;left:111px;top:2543px;width:977px;height:367px}
.compare-before{position:absolute;left:0;top:0;width:486px;height:367px;background:linear-gradient(160deg,#0c5b43 0%,#2f7d63 50%,#4b8e73 100%)}
.compare-after{position:absolute;left:490px;top:0;width:487px;height:367px;background:linear-gradient(170deg,#1f2a17 0%,#4f5a2a 40%,#8c7a34 70%,#3c4a2a 100%)}
.compare-handle{position:absolute;left:456px;top:152px;width:64px;height:64px}

/* testimonials */
.clients .section-title{position:absolute;left:0;top:2990px;width:1200px}
.review{position:absolute;top:3084px;width:297px;height:291px;border:1.5px solid var(--line);border-radius:8px;padding:22px 22px 0}
.review-top{display:flex;justify-content:space-between;align-items:center}
.review p{margin-top:20px;font-size:12.5px;line-height:20.6px;color:var(--muted)}
.reviewer{position:absolute;left:22px;top:216px;display:flex;align-items:center;gap:15px}
.avatar{width:44px;height:44px;border-radius:50%;background:var(--green-dark);color:var(--white);font-size:18px;font-weight:500;display:flex;align-items:center;justify-content:center}
.reviewer strong{display:block;font-size:14px;font-weight:500}
.reviewer span{font-size:11px;color:#9a9e9b}
.dots{position:absolute;left:564px;top:3413px;display:flex;gap:7px;align-items:center}
.dots i{width:11px;height:11px;border-radius:50%;background:#8c8f8d}
.dots i.on{width:15px;height:15px;background:var(--green-dark)}

/* discount */
.discount{position:absolute;left:0;top:3514px;width:1200px;height:209px;background:var(--ivory)}
.discount h2{position:absolute;left:113px;top:55px;font-size:25px;font-weight:600;color:var(--green-dark)}
.discount p{position:absolute;left:113px;top:105px;width:570px;font-size:18px;line-height:26px;color:var(--muted)}
.discount .btn{position:absolute;left:829px;top:108px;line-height:38px;padding:0 16px}

/* footer */
.site-footer{position:absolute;left:0;top:3723px;width:1200px;height:263px;background:var(--green-dark);color:var(--white)}
.footer-brand{position:absolute;left:0;top:70px;width:1200px;text-align:center;font-size:30px;font-weight:600;color:var(--yellow)}
.footer-nav{position:absolute;left:0;top:157px;width:1200px;display:flex;justify-content:center;gap:56px;font-size:20px}
.footer-line{position:absolute;left:0;top:199px;width:1200px;height:1px;background:rgba(255,255,255,.6)}
.copyright{position:absolute;left:0;top:214px;width:1200px;text-align:center;font-size:14px}
</style>
</head>
<body>

<header class="site-header">
  <a class="brand" href="#"><span class="brand-dot"></span>Corwin Beacon Lighting</a>
  <nav class="main-nav">
    <a class="active" href="#">Home</a><a href="#">About Us</a><a href="#">Services</a><a href="#">Contact Us</a>
  </nav>
</header>

<section class="hero">
  <div class="hero-photo" role="img" aria-label="Modern home at dusk with landscape lighting along garden beds"></div>
  <h1 class="hero-title">Illuminate with Confidence.<br>Designed with Precision.<br>Installed with Care.</h1>
  <p class="hero-text">Locally and veteran-owned, we take pride in transforming outdoor spaces through innovative lighting solutions tailored to your vision</p>
  <a class="btn" href="#">Schedule Your Free Estimate</a>
</section>

<section class="services">
  <h2 class="section-title">What We Do</h2>
  <article class="service" style="left:111px">
    <div class="service-photo" role="img" aria-label="Garden path lit by bollard lights at night" style="background:linear-gradient(150deg,#2b2a1f 0%,#6b5a2a 45%,#2f4a25 100%)"></div>
    <h3>Landscape Design</h3>
    <ul>
      <li><svg width="11" height="9" viewBox="0 0 11 9"><path d="M1 4.5l3 3 6-6.5" fill="none" stroke="#17644a" stroke-width="1.6"/></svg>Lorem ipsum dolor sit amet,</li>
      <li><svg width="11" height="9" viewBox="0 0 11 9"><path d="M1 4.5l3 3 6-6.5" fill="none" stroke="#17644a" stroke-width="1.6"/></svg>Consectetur adipiscing</li>
      <li><svg width="11" height="9" viewBox="0 0 11 9"><path d="M1 4.5l3 3 6-6.5" fill="none" stroke="#17644a" stroke-width="1.6"/></svg>Eiusmod tempor incididunt ut</li>
    </ul>
    <a class="more" href="#">View More</a>
  </article>
  <article class="service" style="left:449px">
    <div class="service-photo" role="img" aria-label="Illuminated stone house facade at twilight" style="background:linear-gradient(180deg,#2f4f86 0%,#4a5f7d 40%,#8a6a3a 70%,#3a3a30 100%)"></div>
    <h3>Landscape Maintenance</h3>
    <ul>
      <li><svg width="11" height="9" viewBox="0 0 11 9"><path d="M1 4.5l3 3 6-6.5" fill="none" stroke="#17644a" stroke-width="1.6"/></svg>Lorem ipsum dolor sit amet,</li>
      <li><svg width="11" height="9" viewBox="0 0 11 9"><path d="M1 4.5l3 3 6-6.5" fill="none" stroke="#17644a" stroke-width="1.6"/></svg>Consectetur adipiscing</li>
      <li><svg width="11" height="9" viewBox="0 0 11 9"><path d="M1 4.5l3 3 6-6.5" fill="none" stroke="#17644a" stroke-width="1.6"/></svg>Eiusmod tempor incididunt ut</li>
    </ul>
    <a class="more" href="#">View More</a>
  </article>
  <article class="service" style="left:787px">
    <div class="service-photo" role="img" aria-label="Technician installing a garden light near a home" style="background:linear-gradient(150deg,#4a3a22 0%,#8a6a34 40%,#2a3a2a 75%,#1e2a2a 100%)"></div>
    <h3>Property Enhancements</h3>
    <ul>
      <li><svg width="11" height="9" viewBox="0 0 11 9"><path d="M1 4.5l3 3 6-6.5" fill="none" stroke="#17644a" stroke-width="1.6"/></svg>Lorem ipsum dolor sit amet,</li>
      <li><svg width="11" height="9" viewBox="0 0 11 9"><path d="M1 4.5l3 3 6-6.5" fill="none" stroke="#17644a" stroke-width="1.6"/></svg>Consectetur adipiscing</li>
      <li><svg width="11" height="9" viewBox="0 0 11 9"><path d="M1 4.5l3 3 6-6.5" fill="none" stroke="#17644a" stroke-width="1.6"/></svg>Eiusmod tempor incididunt ut</li>
    </ul>
    <a class="more" href="#">View More</a>
  </article>
</section>

<section class="demo-band">
  <p>Try Before You Buy And Experience Your Home In A Whole New Light With Our Complimentary Demo Kit</p>
  <a class="btn" href="#">Try Before You Buy</a>
</section>

<section class="story">
  <h2 class="story-title">Our Story</h2>
  <p class="story-text">Derek is retired Army and he opened a fitness studio in 2017 with his wife Jolene. He has installed low voltage lighting in every home he lived in and for his friends and family over the years and decided to open his own business because he is passionate about beautifying outdoor landscapes and highlighting a properties full potential, not only in the day but at night as well all while providing safety and security for his clients.</p>
  <a class="btn" href="#">Read More</a>
  <div class="story-photo" role="img" aria-label="Business owner at his desk checking his phone"></div>
</section>

<section class="features">
  <div class="feature" style="left:105px">
    <svg class="feature-icon" viewBox="0 0 136 136"><circle cx="68" cy="68" r="66" fill="none" stroke="#17644a" stroke-width="2.5"/><circle cx="68" cy="68" r="59" fill="#17644a"/><path d="M68 48a16 16 0 0 0-9 29v7h18v-7a16 16 0 0 0-9-29z" fill="#fff"/><rect x="60" y="87" width="16" height="4" rx="2" fill="#fff"/><path d="M68 32v7M44 42l5 5M92 42l-5 5M36 66h7M100 66h-7" stroke="#fff" stroke-width="4" stroke-linecap="round"/></svg>
    Illuminate with<br>Confidence
  </div>
  <div class="feature-sep" style="left:327px"></div>
  <div class="feature" style="left:362px">
    <svg class="feature-icon" viewBox="0 0 136 136"><circle cx="68" cy="68" r="66" fill="none" stroke="#17644a" stroke-width="2.5"/><circle cx="68" cy="68" r="59" fill="#17644a"/><path d="M68 36l26 9v20c0 18-12 30-26 36-14-6-26-18-26-36V45z" fill="#fff"/><circle cx="68" cy="66" r="13" fill="none" stroke="#17644a" stroke-width="3.5"/><path d="M62 66l4 4 8-8" fill="none" stroke="#17644a" stroke-width="3.5"/></svg>
    Enhanced<br>Safety &amp; Security
  </div>
  <div class="feature-sep" style="left:594px"></div>
  <div class="feature" style="left:633px">
    <svg class="feature-icon" viewBox="0 0 136 136"><circle cx="68" cy="68" r="66" fill="none" stroke="#17644a" stroke-width="2.5"/><circle cx="68" cy="68" r="59" fill="#17644a"/><circle cx="68" cy="68" r="27" fill="none" stroke="#fff" stroke-width="6" stroke-dasharray="10 5"/><path d="M78 50a12 12 0 0 0-13 16L50 81l5 5 15-15a12 12 0 0 0 16-13l-7 7-6-2-2-6z" fill="#fff"/></svg>
    Quarterly<br>Maintenance Plans
  </div>
  <div class="feature-sep" style="left:871px"></div>
  <div class="feature" style="left:899px">
    <svg class="feature-icon" viewBox="0 0 136 136"><circle cx="68" cy="68" r="66" fill="none" stroke="#17644a" stroke-width="2.5"/><circle cx="68" cy="68" r="59" fill="#17644a"/><path d="M50 44h14a7 7 0 1 1 12 0h10v18a7 7 0 1 1 0 12v20H50V76a7 7 0 1 0 0-12z" fill="#fff"/></svg>
    Free Estimates,<br>No Pressure
  </div>
</section>

<div class="projects-bg"></div>
<section class="projects">
  <h2 class="projects-title">Latest<br>Landscape Lighting<br>Projects</h2>
  <p class="projects-text">Lorem ipsum dolor sit amet, consectetur adipiscing elit, sed do eiusmod tempor incididunt ut labore et dolore magna aliqua. Ut enim ad minim veniam, quis nostrud exercitation ullamco laboris nisi ut aliquip</p>
  <div class="compare">
    <div class="compare-before" role="img" aria-label="Garden bed before lighting installation"></div>
    <div class="compare-after" role="img" aria-label="Same garden path lit warmly after installation"></div>
    <svg class="compare-handle" viewBox="0 0 64 64"><circle cx="32" cy="32" r="31" fill="#fff"/><path d="M28 20L16 32l12 12zM36 20l12 12-12 12z" fill="#17644a"/></svg>
  </div>
</section>

<section class="clients">
  <h2 class="section-title">What Our Clients Say</h2>
  <article class="review" style="left:111px">
    <div class="review-top"><svg width="24" height="18" viewBox="0 0 24 18"><path d="M0 18V10C0 4 3 1 9 0v4c-3 1-4 3-4 5h4v9zM14 18V10c0-6 3-9 9-10v4c-3 1-4 3-4 5h4v9z" fill="#1f2a24"/></svg><svg width="64" height="11" viewBox="0 0 64 11" fill="#f39c12"><path id="st" d="M5.5 0l1.6 3.6 3.9.3-3 2.5.9 3.8-3.4-2-3.4 2 .9-3.8-3-2.5 3.9-.3z"/><use href="#st" x="13"/><use href="#st" x="26"/><use href="#st" x="39"/><use href="#st" x="52"/></svg></div>
    <p>Lorem ipsum dolor sit amet, consectetur adipiscing elit, sed do eiusmod tempor incididunt ut labore et dolore magna aliqua. Quis ipsum suspendisse ultrices gravida. Risus commodo viverra maecenas accumsan</p>
    <div class="reviewer"><div class="avatar">NW</div><div><strong>Nora Whitfield</strong><span>MD at Oakline Group</span></div></div>
  </article>
  <article class="review" style="left:451px">
    <div class="review-top"><svg width="24" height="18" viewBox="0 0 24 18"><path d="M0 18V10C0 4 3 1 9 0v4c-3 1-4 3-4 5h4v9zM14 18V10c0-6 3-9 9-10v4c-3 1-4 3-4 5h4v9z" fill="#1f2a24"/></svg><svg width="64" height="11" viewBox="0 0 64 11" fill="#f39c12"><use href="#st"/><use href="#st" x="13"/><use href="#st" x="26"/><use href="#st" x="39"/><use href="#st" x="52"/></svg></div>
    <p>Lorem ipsum dolor sit amet, consectetur adipiscing elit, sed do eiusmod tempor incididunt ut labore et dolore magna aliqua. Quis ipsum suspendisse ultrices gravida. Risus commodo viverra maecenas accumsan</p>
    <div class="reviewer"><div class="avatar">NW</div><div><strong>Nora Whitfield</strong><span>MD at Oakline Group</span></div></div>
  </article>
  <article class="review" style="left:793px">
    <div class="review-top"><svg width="24" height="18" viewBox="0 0 24 18"><path d="M0 18V10C0 4 3 1 9 0v4c-3 1-4 3-4 5h4v9zM14 18V10c0-6 3-9 9-10v4c-3 1-4 3-4 5h4v9z" fill="#1f2a24"/></svg><svg width="64" height="11" viewBox="0 0 64 11" fill="#f39c12"><use href="#st"/><use href="#st" x="13"/><use href="#st" x="26"/><use href="#st" x="39"/><use href="#st" x="52"/></svg></div>
    <p>Lorem ipsum dolor sit amet, consectetur adipiscing elit, sed do eiusmod tempor incididunt ut labore et dolore magna aliqua. Quis ipsum suspendisse ultrices gravida. Risus commodo viverra maecenas accumsan</p>
    <div class="reviewer"><div class="avatar">NW</div><div><strong>Nora Whitfield</strong><span>MD at Oakline Group</span></div></div>
  </article>
  <div class="dots"><i class="on"></i><i></i><i></i><i></i></div>
</section>

<section class="discount">
  <h2>10% Discount for Military, Veterans &amp; First Responders</h2>
  <p>As a veteran-owned business, we understand the value of service and sacrifice. That’s why we proudly offer</p>
  <a class="btn" href="#">Schedule Your Free Estimate</a>
</section>

<footer class="site-footer">
  <div class="footer-brand">Corwin Beacon Lighting</div>
  <nav class="footer-nav"><a href="#">Home</a><a href="#">About Us</a><a href="#">Services</a><a href="#">Contact Us</a></nav>
  <div class="footer-line"></div>
  <p class="copyright">Copyright © 2025 Corwin Beacon Lighting. All rights reserved.</p>
</footer>

</body>
</html>
```